Business Card Design Project

Looking to update our business cards. We have a logo with our slogan. We are an IT firm so we wouldlike a modern look.

Industry/Entity Type

Business

```html
<!DOCTYPE html>
<html lang="en">
<head>
<meta charset="utf-8">
<title>Clearpath Inc — Business Card</title>
<link rel="stylesheet" href="https://fonts.googleapis.com/css2?family=Josefin+Sans:wght@400;600&family=Tinos&display=swap">
<style>
  :root {
    --backdrop: #3b2a22;
    --card-edge: #4f6a32;
    --card-glow: #3f9a4a;
    --band-light: #f4f4f4;
    --band-dark: #d6d6d6;
    --brand-green: #5b7a2f;
    --ink: #1f1f1f;
  }
  * { margin: 0; padding: 0; box-sizing: border-box; }
  html, body {
    width: 1200px;
    height: 1181px;
    overflow: hidden;
    background: var(--backdrop);
  }
  .sheet { position: relative; width: 1200px; height: 1181px; }
  .card {
    position: absolute;
    left: 236px;
    width: 727px;
    height: 418px;
    overflow: hidden;
    background: radial-gradient(ellipse 55% 60% at 50% 50%, var(--card-glow) 0%, var(--card-edge) 100%);
  }
  .card--front { top: 124px; }
  .card--back  { top: 628px; }
  .band {
    position: absolute;
    left: 0;
    top: 158px;
    width: 100%;
    height: 103px;
    background: linear-gradient(180deg, var(--band-light) 0%, #e8e8e8 55%, var(--band-dark) 100%);
    box-shadow: 0 2px 4px rgba(0,0,0,0.25);
  }
  .brand {
    position: absolute;
    left: 0;
    width: 100%;
    text-align: center;
    font-family: "Josefin Sans", sans-serif;
    white-space: nowrap;
  }
  .brand__name {
    top: 18px;
    font-size: 40px;
    font-weight: 600;
    letter-spacing: 4px;
    color: var(--brand-green);
  }
  .brand__slogan {
    top: 70px;
    font-size: 15px;
    font-weight: 600;
    letter-spacing: 5.5px;
    color: var(--ink);
  }
  .contact {
    position: absolute;
    top: 44px;
    font-family: "Tinos", serif;
    font-size: 16px;
    color: var(--ink);
    white-space: nowrap;
    display: flex;
    align-items: center;
    gap: 8px;
  }
  .contact__mark {
    width: 8px;
    height: 8px;
    background: var(--ink);
    display: inline-block;
  }
  .contact--phone { left: 58px; }
  .contact--web   { left: 267px; }
  .contact--email { left: 505px; }
</style>
</head>
<body>
  <main class="sheet">
    <section class="card card--front" aria-label="Card front">
      <div class="band">
        <div class="brand brand__name">CLEARPATH INC</div>
        <div class="brand brand__slogan">KEEPING SYSTEMS RUNNING</div>
      </div>
    </section>

    <section class="card card--back" aria-label="Card back">
      <div class="band">
        <p class="contact contact--phone">Phone <span class="contact__mark"></span> 0123456789</p>
        <p class="contact contact--web">Web <span class="contact__mark"></span> www.website.com</p>
        <p class="contact contact--email">Email <span class="contact__mark"></span> name@email.com</p>
      </div>
    </section>
  </main>
</body>
</html>
```